New Webpage for High Class Expert Witness Services Company

We are looking for a minimalist design for a webpage that just has our logo and an entry form offer to connect with one of our Liaisons.
The entry form should just ask for Name, Email, Contact Info and Description of Project.

Company Name is: The Marlowe Crest Advisory Services

Number of Pages Required

1 page

```html
<!DOCTYPE html>
<html lang="en">
<head>
<meta charset="utf-8">
<title>Marlowe Crest Advisory Services — Request a Confidential Consultation</title>
<link href="https://fonts.googleapis.com/css2?family=Cinzel:wght@500;600&family=Poppins:wght@400;500&display=swap" rel="stylesheet">
<style>
  :root {
    --ink: #121212;
    --header-bg: #131313;
    --logo-silver: #d2d2d2;
    --page-bg: #ffffff;
    --field-border: #a8a8a8;
    --placeholder: #6c6c6c;
    --button-text: #ffffff;
  }
  * { box-sizing: border-box; margin: 0; padding: 0; }
  html, body {
    width: 1200px;
    height: 1137px;
    overflow: hidden;
    background: var(--page-bg);
    color: var(--ink);
    font-family: "Poppins", Arial, sans-serif;
  }
  .page { position: relative; width: 1200px; height: 1137px; }

  .site-header {
    position: absolute; left: 0; top: 0;
    width: 1200px; height: 210px;
    background: var(--header-bg);
    display: flex; align-items: center; justify-content: center;
  }
  .brand { display: flex; align-items: center; gap: 18px; }
  .brand-mark {
    width: 54px; height: 54px;
    background: var(--logo-silver);
  }
  .brand-name {
    font-family: "Cinzel", "Times New Roman", serif;
    font-weight: 600;
    font-size: 34px;
    line-height: 1.15;
    letter-spacing: 2px;
    color: var(--logo-silver);
    text-transform: uppercase;
  }

  .page-title {
    position: absolute; left: 0; top: 262px; width: 1200px;
    text-align: center;
    font-family: "Cinzel", "Times New Roman", serif;
    font-weight: 600;
    font-size: 38px;
    line-height: 50px;
    letter-spacing: 0.5px;
    color: var(--ink);
  }

  .consult-form { position: absolute; left: 198px; top: 0; width: 820px; }
  .field-label {
    position: absolute;
    font-weight: 500;
    font-size: 15.5px;
    text-transform: uppercase;
    color: var(--ink);
    white-space: nowrap;
  }
  .field-input {
    position: absolute;
    border: 1px solid var(--field-border);
    border-radius: 6px;
    background: var(--page-bg);
    font-family: "Poppins", Arial, sans-serif;
    font-size: 16.5px;
    color: var(--ink);
    padding: 0 18px;
    height: 62px;
    outline: none;
  }
  .field-input::placeholder { color: var(--placeholder); }
  textarea.field-input { padding: 18px; resize: none; height: 148px; }

  .label-name { left: 0; top: 416px; }
  .label-email { left: 419px; top: 416px; }
  .input-name { left: 0; top: 456px; width: 401px; }
  .input-email { left: 419px; top: 456px; width: 401px; }
  .label-contact { left: 0; top: 552px; }
  .input-contact { left: 0; top: 592px; width: 820px; }
  .label-description { left: 4px; top: 690px; }
  .input-description { left: 0; top: 730px; width: 820px; }

  .submit-button {
    position: absolute; left: 1px; top: 897px;
    width: 818px; height: 61px;
    border: none; border-radius: 5px;
    background: var(--ink);
    color: var(--button-text);
    font-family: "Poppins", Arial, sans-serif;
    font-size: 16.5px;
    text-transform: uppercase;
    cursor: pointer;
  }

  .privacy-note {
    position: absolute; left: 0; top: 993px; width: 1200px;
    text-align: center; font-size: 14px;
  }
  .site-footer {
    position: absolute; left: 0; top: 1049px; width: 1200px;
    text-align: center; font-size: 14px; line-height: 24px;
  }
</style>
</head>
<body>
<div class="page">
  <header class="site-header">
    <div class="brand">
      <div class="brand-mark" aria-hidden="true"></div>
      <div class="brand-name">Marlowe Crest<br>Advisory Services</div>
    </div>
  </header>

  <h1 class="page-title">Request a<br>Confidential Consultation</h1>

  <form class="consult-form">
    <label class="field-label label-name" for="full-name">Full Name</label>
    <input class="field-input input-name" id="full-name" type="text" placeholder="Enter your Name">

    <label class="field-label label-email" for="email">Email Address</label>
    <input class="field-input input-email" id="email" type="email" placeholder="Enter your Email">

    <label class="field-label label-contact" for="contact">Contact Info</label>
    <input class="field-input input-contact" id="contact" type="text" placeholder="Enter your Phone, Address or Somthing Else">

    <label class="field-label label-description" for="description">Description of Project</label>
    <textarea class="field-input input-description" id="description" placeholder="Enter your Brief Description of the Project"></textarea>

    <button class="submit-button" type="button">Request Consultation</button>
  </form>

  <p class="privacy-note">All inquiries are handled with strict confidentiality. A liaison will respond promptly.</p>

  <footer class="site-footer">
    © 2026. The Marlowe Crest Advisory Services.<br>All Rights Reserved.
  </footer>
</div>
</body>
</html>
```